PeakRoamJourneys

1. Can you describe what your company does?

Please find enclosed documents for your reference about our business doing.

2. Who are your target customers for the website?

Company Positioning: A comprehensive supplier of premier international sports travel and high-end event services.
Core Advantage: Exclusive international partnership resources and an Official Ticketing Assurance System.
Service Standard: One-Stop, High-Quality Service Solutions based on the "An once-in-a-lifetime experience" philosophy.

Our target customers for the website:
Mid-to-High-end Sports Enthusiasts
Corporate Clients
Sports Associations
Please kindly find enclosed for more details about our target customers, I think it's very important to make it clear to you.

3. Do you have an existing domain name / website address?

Yes, I have. I just applied for this new domain and it's totally a new website. www.peakroamjourneys.example

4. In addition to a Home Page, which other pages / sections would you like your website to have:
About Us
Contact Us , Office / Mailing Address
Sports Travel Products( Bucket Lists) : Globe Shield, Royal Quartet, Vantara Games, Football, KHL, Golf, Skiing, Hiking,Galas
Reviews/ Unforgettable Moments
FAQs
Any other page / section you would like: Here is the website for your reference, www.lanewander.example
For each of the pages / sections you’d like to have, please provide the text (and images, if available) you would like to include.
Please recommend 2-3 templates to me, and let me know what kind of text I will provide to every web pages.

5. Which of the below are features and functionalities your website will need:
Image Gallery
Videos
Contact Form
Maps
FAQs
6. Please provide the URLs for the social media profiles you'd like to link to the website.

Do you know Bright Lantern App?

Please let me know anything you need, thank you very much!

Have a good day!

Target Market(s)

Travel for the world-wide sports games and make an once-in-a-lifetime experience

Industry/Entity Type

sports and travel industry

Coding

Number of Pages Required

5+ page

Requirements
Must have
• our logo
Nice to have
• On the homepage, I’d like a banner-style section to prominently showcase the latest products.

```html
<!DOCTYPE html>
<html lang="en">
<head>
<meta charset="utf-8">
<title>PeakRoamJourneys – Premier Sports Travel</title>
<link href="https://fonts.googleapis.com/css2?family=Bebas+Neue&family=Montserrat:wght@400;500;600;700&display=swap" rel="stylesheet">
<style>
:root{
  --teal:#1fbccb;
  --red:#e8141a;
  --navy:#0f2740;
  --navy-2:#1b3553;
  --ink:#1d1d1f;
  --muted:#6b6b70;
  --soft:#f5f5f5;
  --white:#ffffff;
}
*{box-sizing:border-box;margin:0;padding:0}
html,body{width:1200px;height:3544px;overflow:hidden}
body{position:relative;font-family:"Montserrat",sans-serif;color:var(--ink);background:var(--white)}
.abs{position:absolute}
.display{font-family:"Bebas Neue",sans-serif;font-weight:400;letter-spacing:-.5px;line-height:1}
.btn{position:absolute;display:flex;align-items:center;justify-content:center;border-radius:30px;font-size:12px;font-weight:600;color:var(--white);background:var(--teal);white-space:nowrap}
.btn-red{background:var(--red)}
.btn-white{background:var(--white);color:var(--ink)}
.photo{position:absolute;overflow:hidden}

/* hero */
.hero{position:absolute;left:0;top:0;width:1200px;height:770px;background:linear-gradient(100deg,var(--navy-2) 0%,#243a58 45%,#6a2e3a 75%,#8c2a2a 100%)}
.brand{position:absolute;font-family:"Montserrat",sans-serif;font-weight:700;color:var(--teal);white-space:nowrap}
.nav{position:absolute;left:383px;top:37px;display:flex;gap:30px;font-size:12px;color:var(--white);font-weight:500;white-space:nowrap}
.header-rule{position:absolute;left:74px;top:89px;width:1050px;height:1px;background:rgba(255,255,255,.45)}
.hero-title{position:absolute;left:74px;top:232px;font-size:55px;line-height:56px;color:var(--white)}
.hero-text{position:absolute;left:77px;top:406px;width:520px;font-size:12px;line-height:19px;color:var(--white)}
.scroll-cue{position:absolute;left:77px;top:656px;width:37px;height:58px;border:1.5px solid var(--white);border-radius:20px}

/* marquee */
.ticker{position:absolute;left:-18px;top:770px;width:1240px;height:56px;background:var(--red);display:flex;align-items:center;gap:26px;white-space:nowrap;overflow:hidden}
.ticker span{font-family:"Bebas Neue",sans-serif;font-size:38px;color:var(--white);line-height:1}
.ticker i{display:inline-block;width:34px;height:34px;border-radius:50%;background:var(--white);flex:none}

/* about */
.about-title{position:absolute;left:637px;top:963px;font-size:38px;line-height:36px}
.about-text{position:absolute;left:637px;width:450px;font-size:11.5px;line-height:18.5px;color:var(--muted)}
.bullets{position:absolute;left:637px;top:1169px;list-style:none;font-size:11.5px;font-weight:600;color:#333}
.bullets li{position:relative;padding-left:18px;height:22.5px}
.bullets li::before{content:"";position:absolute;left:1px;top:5px;width:8px;height:8px;border-radius:50%;background:var(--red)}

/* features */
.features{position:absolute;left:0;top:1463px;width:1200px;height:367px;background:var(--soft)}
.section-title{position:absolute;left:0;width:1200px;text-align:center;font-size:40px}
.feature{position:absolute;top:1606px;width:320px;text-align:center}
.feature .icon{width:64px;height:64px;border-radius:50%;margin:0 auto 14px;display:flex;align-items:center;justify-content:center}
.feature h3{font-family:"Bebas Neue",sans-serif;font-weight:400;font-size:21px;letter-spacing:-.2px}
.feature p{margin-top:6px;font-size:11.5px;line-height:19px;color:var(--muted)}
.vrule{position:absolute;top:1600px;width:1px;height:148px;background:#cfcfd4}

/* bucket list */
.section-sub{position:absolute;left:0;width:1200px;text-align:center;font-size:11.5px;line-height:19px;color:var(--muted)}
.trip{position:absolute;top:2041px;width:252px;height:301px;border-radius:16px;overflow:hidden}
.trip h4{position:absolute;left:0;right:0;bottom:22px;text-align:center;font-family:"Bebas Neue",sans-serif;font-weight:400;font-size:24px;color:var(--white)}
.trip.featured h4{text-align:left;left:25px;bottom:62px}
.trip p{position:absolute;left:25px;bottom:20px;width:210px;font-size:11px;line-height:18px;color:var(--white)}

/* reviews */
.review{position:absolute;top:2587px;width:336px;height:179px;border-radius:20px;background:#f6f6f7}
.avatar{position:absolute;left:22px;top:20px;width:72px;height:72px;border-radius:50%}
.review h5{position:absolute;left:105px;top:32px;font-family:"Bebas Neue",sans-serif;font-weight:400;font-size:20px}
.stars{position:absolute;left:105px;top:56px;display:flex;gap:2px}
.review p{position:absolute;left:22px;top:106px;width:290px;font-size:11px;line-height:19px;color:var(--muted)}

/* cta & footer */
.footer{position:absolute;left:0;top:3089px;width:1200px;height:455px;background:var(--navy)}
.cta{position:absolute;left:151px;top:2958px;width:898px;height:216px;border-radius:26px;background:var(--red);background-image:radial-gradient(rgba(0,0,0,.08) 1px,transparent 1.4px);background-size:6px 6px}
.cta-title{position:absolute;left:200px;top:3002px;font-size:37px;color:var(--white)}
.cta-text{position:absolute;left:201px;top:3053px;font-size:11.5px;color:var(--white)}
.foot-h{position:absolute;top:3257px;font-family:"Bebas Neue",sans-serif;font-size:22px;color:var(--white)}
.foot-links{position:absolute;left:327px;top:3284px;list-style:none;font-size:11px;color:var(--white)}
.foot-links li{height:22.5px}
.contact-item{position:absolute;left:577px;font-size:10.5px;line-height:15px;color:var(--white)}
.contact-icon{position:absolute;left:553px}
.subscribe-input{position:absolute;left:816px;top:3320px;width:308px;height:39px;border-radius:22px;background:var(--white);font-size:11px;color:#888;padding:12px 0 0 27px}
.foot-rule{position:absolute;left:74px;top:3479px;width:1050px;height:1px;background:rgba(255,255,255,.35)}
.social{position:absolute;top:3497px;width:31px;height:31px;border-radius:50%;background:rgba(255,255,255,.22)}
</style>
</head>
<body>

<!-- HERO -->
<section class="hero">
  <div class="brand" style="left:74px;top:14px;font-size:22px;line-height:26px">PeakRoam</div>
  <div class="abs" style="left:75px;top:44px;font-size:7.5px;color:var(--white);white-space:nowrap">An Once-in-a-lifetime Experience!</div>
  <nav class="nav"><span>Home</span><span>About Us</span><span>Sports Travel Products</span><span>Reviews</span><span>FAQs</span><span>Contact Us</span></nav>
  <div class="btn" style="left:936px;top:23px;width:188px;height:42px">Plan Your Experience</div>
  <div class="header-rule"></div>

  <h1 class="hero-title display">EXPERIENCE THE WORLD’S<br>GREATEST SPORTING MOMENTS –<br>LIVE AND IN LUXURY.</h1>
  <p class="hero-text">From the Globe Shield to the Vantara Games, PeakRoamJourneys takes you beyond the stands with official access, VIP hospitality, and unforgettable travel experiences — designed exclusively for you.</p>
  <div class="btn" style="left:74px;top:480px;width:216px;height:43px">Explore Bucket List Trips</div>
  <div class="btn btn-red" style="left:299px;top:480px;width:170px;height:43px">Start Planning Now</div>
  <div class="scroll-cue">
    <svg width="34" height="55" viewBox="0 0 34 55"><path d="M17 19v17M12 31l5 5 5-5" fill="none" stroke="#fff" stroke-width="1.5"/></svg>
  </div>

  <div class="photo" role="img" aria-label="Female footballer in a red kit sprinting after a ball" style="left:626px;top:138px;width:495px;height:578px;border-radius:40px;background:radial-gradient(ellipse at 55% 50%,rgba(200,40,45,.55),rgba(140,40,45,0) 65%)"></div>
</section>

<!-- TICKER -->
<div class="ticker">
  <span>PeakRoam</span><i></i><span>PeakRoam</span><i></i><span>PeakRoam</span><i></i><span>PeakRoam</span><i></i><span>PeakRoam</span><i></i><span>PeakRoam</span><i></i><span>PeakRoam</span><i></i><span>PeakRoam</span><i></i>
</div>

<!-- ABOUT -->
<section>
  <div class="photo" role="img" aria-label="Couple in a convertible driving a coastal road at sunset" style="left:116px;top:923px;width:476px;height:437px;border-radius:28px;background:linear-gradient(180deg,#3f4f63 0%,#d98a3c 40%,#f2b154 50%,#5b4030 70%,#1e1a18 100%)"></div>
  <h2 class="about-title display">YOUR PREMIER PARTNER IN GLOBAL<br>SPORTS TRAVEL.</h2>
  <p class="about-text" style="top:1049px">Since 2009, PeakRoamJourneys has been crafting once-in-a-lifetime experiences for sports enthusiasts, corporate clients, and professional teams.</p>
  <p class="about-text" style="top:1099px">As a fully licensed outbound travel operator, we connect you directly with the world’s most prestigious sports events — offering secure, official access and seamless, luxury-level service from start to finish.</p>
  <ul class="bullets">
    <li>Official Ticketing Assurance.</li>
    <li>Exclusive International Partnerships.</li>
    <li>One-Stop Premium Service Solutions.</li>
    <li>Over a Decade of Trusted Experience.</li>
  </ul>
  <div class="btn" style="left:637px;top:1277px;width:123px;height:40px">Read More</div>
</section>

<!-- FEATURES -->
<section class="features"></section>
<h2 class="section-title display" style="top:1531px">MORE THAN A TRIP – IT’S AN EXPERIENCE.</h2>
<div class="vrule" style="left:399px"></div>
<div class="vrule" style="left:802px"></div>
<div class="feature" style="left:73px">
  <div class="icon" style="background:var(--teal)"><svg width="34" height="34" viewBox="0 0 34 34" fill="none" stroke="#fff" stroke-width="1.6"><circle cx="17" cy="14" r="4"/><circle cx="8" cy="17" r="3"/><circle cx="26" cy="17" r="3"/><path d="M10 29c0-5 3-8 7-8s7 3 7 8M3 28c0-4 2-6 5-6M31 28c0-4-2-6-5-6M12 6l2 3 3-4 3 4 2-3"/></svg></div>
  <h3>EXCLUSIVE ACCESS</h3>
  <p>We secure official tickets and VIP entry to<br>the world’s top sporting events.</p>
</div>
<div class="feature" style="left:440px">
  <div class="icon" style="background:var(--red)"><svg width="34" height="34" viewBox="0 0 34 34" fill="none" stroke="#fff" stroke-width="1.6"><path d="M17 18l-5-5a3 3 0 0 1 5-3 3 3 0 0 1 5 3z"/><path d="M5 12v9l6 8M29 12v9l-6 8M9 18l4 5M25 18l-4 5"/></svg></div>
  <h3>ONCE-IN-A-LIFETIME QUALITY</h3>
  <p>Every journey reflects our belief: an experience worth<br>remembering forever.</p>
</div>
<div class="feature" style="left:807px">
  <div class="icon" style="background:var(--teal)"><svg width="34" height="34" viewBox="0 0 34 34" fill="none" stroke="#fff" stroke-width="1.6"><circle cx="19" cy="13" r="7"/><circle cx="19" cy="13" r="2.5"/><path d="M19 3v3M19 20v3M9 13h3M26 13h3M4 24l6-3 7 2h5M4 30l5-1 10 1 9-6"/></svg></div>
  <h3>SEAMLESS SERVICE</h3>
  <p>From flights to finish line, we handle every<br>detail with precision and care.</p>
</div>

<!-- BUCKET LIST -->
<h2 class="section-title display" style="top:1925px">YOUR SPORTS TRAVEL BUCKET LIST AWAITS.</h2>
<p class="section-sub" style="top:1974px">Step into the world’s most iconic arenas and feel the adrenaline live — with packages<br>tailored to your dream events.</p>
<div class="trip" role="img" aria-label="Golden trophy on a stadium pitch" style="left:76px;background:linear-gradient(180deg,#6d7a86 0%,#8a7a4c 45%,#3b5a2c 80%,#2b3f21 100%)"><h4>GLOBE SHIELD CUP</h4></div>
<div class="trip" role="img" aria-label="Athlete celebrating with a flag in an arena" style="left:341px;background:linear-gradient(180deg,#5f6e86 0%,#4968a8 50%,#2c3358 100%)"><h4>VANTARA GAMES</h4></div>
<div class="trip featured" role="img" aria-label="Tennis player at an indoor court with a cart of balls" style="left:607px;background:linear-gradient(180deg,#3d4f6c 0%,#5f7a8c 40%,#2b3d55 100%)"><h4>ROYAL QUARTET TENNIS</h4><p>From Ashgrove Lawn to the Harborview Open, courtside in luxury.</p></div>
<div class="trip" role="img" aria-label="Golfer in a patterned outfit on a fairway" style="left:872px;background:linear-gradient(180deg,#4f5a55 0%,#5b7a45 50%,#3c5a2a 100%)"><h4>GOLF &amp; MERIDIAN CUP</h4></div>
<div class="btn" style="left:504px;top:2382px;width:191px;height:40px">View All Experiences</div>

<!-- REVIEWS -->
<h2 class="section-title display" style="top:2518px">WHAT OUR CLIENTS SAY</h2>
<div class="review" style="left:76px">
  <div class="avatar" role="img" aria-label="Client portrait" style="background:linear-gradient(160deg,#c9d6e3,#5b88b5)"></div>
  <h5>– DANIEL R., LONDON</h5>
  <div class="stars"><svg width="78" height="14" viewBox="0 0 78 14" fill="#f2a320"><g id="s"><polygon points="7,0 9,5 14,5 10,8 11.5,13 7,10 2.5,13 4,8 0,5 5,5"/></g><use href="#s" x="16"/><use href="#s" x="32"/><use href="#s" x="48"/><use href="#s" x="64"/></svg></div>
  <p>“Watching the Globe Shield live was surreal! Everything was perfectly organized from tickets to transfers.”</p>
</div>
<div class="review" style="left:431px">
  <div class="avatar" role="img" aria-label="Client portrait" style="background:linear-gradient(160deg,#d2c8bb,#7a6a58)"></div>
  <h5>– NORTHLANE EVENTS</h5>
  <div class="stars"><svg width="78" height="14" viewBox="0 0 78 14" fill="#f2a320"><use href="#s"/><use href="#s" x="16"/><use href="#s" x="32"/><use href="#s" x="48"/><use href="#s" x="64"/></svg></div>
  <p>“Our corporate incentive trip during the Royal Quartet was world class. Every detail exceeded expectations.”</p>
</div>
<div class="review" style="left:787px">
  <div class="avatar" role="img" aria-label="Client portrait" style="background:linear-gradient(160deg,#b7c9b0,#3a63a8)"></div>
  <h5>– AIKO M., TOKYO</h5>
  <div class="stars"><svg width="78" height="14" viewBox="0 0 78 14" fill="#f2a320"><use href="#s"/><use href="#s" x="16"/><use href="#s" x="32"/><use href="#s" x="48"/><use href="#s" x="64"/></svg></div>
  <p>“The VIP Vantara Games experience was truly once in a lifetime. Thank you PeakRoamJourneys!”</p>
</div>
<div class="btn" style="left:504px;top:2804px;width:191px;height:42px">See More Memories</div>

<!-- CTA + FOOTER -->
<footer class="footer"></footer>
<div class="cta"></div>
<div class="photo" role="img" aria-label="Footballer in a red kit striking a ball" style="left:800px;top:2900px;width:150px;height:265px;border-radius:30px;background:linear-gradient(180deg,rgba(190,30,35,.35),rgba(190,30,35,.15))"></div>
<h2 class="cta-title display">YOUR ONCE-IN-A-LIFETIME JOURNEY STARTS HERE.</h2>
<p class="cta-text">Join the world’s elite sports travelers. Let’s design an experience you’ll never forget.</p>
<div class="btn" style="left:201px;top:3088px;width:173px;height:40px">Plan Your Experience</div>
<div class="btn btn-white" style="left:384px;top:3088px;width:173px;height:40px">Contact Our Team</div>

<div class="brand" style="left:74px;top:3310px;font-size:26px;line-height:30px">PeakRoam</div>
<div class="abs" style="left:75px;top:3378px;font-size:8.5px;color:var(--white);white-space:nowrap">An Once-in-a-lifetime Experience!</div>

<div class="foot-h" style="left:326px">QUICK LINKS</div>
<ul class="foot-links"><li>Home</li><li>About Us</li><li>Sports Travel</li><li>Products</li><li>Reviews</li><li>FAQs</li><li>Contact</li></ul>

<div class="foot-h" style="left:555px">CONTACT US</div>
<svg class="contact-icon" style="top:3290px" width="14" height="14" viewBox="0 0 14 14"><path d="M3 1l2.5 2.5-1.5 2a8 8 0 0 0 4.5 4.5l2-1.5L13 11l-2 2C5 13 1 9 1 3z" fill="var(--teal)"/></svg>
<div class="contact-item" style="top:3287px">Phone:<br>+00 555 010 246</div>
<svg class="contact-icon" style="top:3335px" width="13" height="10" viewBox="0 0 13 10"><rect width="13" height="10" rx="1.5" fill="var(--teal)"/><path d="M1 1.5l5.5 4 5.5-4" fill="none" stroke="var(--navy)" stroke-width="1.2"/></svg>
<div class="contact-item" style="top:3332px">Email:<br>info@peakroamjourneys.example</div>
<svg class="contact-icon" style="top:3378px" width="12" height="15" viewBox="0 0 12 15"><path d="M6 0a6 6 0 0 1 6 6c0 4-6 9-6 9S0 10 0 6a6 6 0 0 1 6-6z" fill="var(--teal)"/><circle cx="6" cy="6" r="2.2" fill="var(--navy)"/></svg>
<div class="contact-item" style="top:3375px">Address:<br>PeakRoamJourneys Ltd.<br>48 Harbor Stadium Lane</div>

<div class="foot-h" style="left:816px">SUBSCRIBE FOR UPDATES</div>
<p class="abs" style="left:816px;top:3290px;font-size:11px;color:var(--white);white-space:nowrap">Subscribe and be the first to receive all the latest</p>
<div class="subscribe-input">Enter Your Email Address...</div>
<svg class="abs" style="left:1088px;top:3332px" width="16" height="16" viewBox="0 0 16 16"><path d="M1 7l14-6-5 14-2-6z" fill="var(--teal)"/></svg>

<div class="foot-rule"></div>
<p class="abs" style="left:74px;top:3507px;font-size:11.5px;color:var(--white)">© 2025 PeakRoamJourneys Ltd. All rights reserved.</p>
<div class="social" style="left:1013px" aria-label="Social profile"></div>
<div class="social" style="left:1052px" aria-label="Social profile"></div>
<div class="social" style="left:1092px" aria-label="Social profile"></div>

</body>
</html>
```